Elegant Business Card with Logo and Picture

Please create a business card that has the Logo colors add Gold and turquoise / use the attached logo - I would like a beautiful Business Card - Please make sure it's printed on both sides / Picture can go on one side Logo other
www.velmoragrove.com
614-372-0583
Lina Suzette Brolin
linasb@quorvamail.com
Life Coach
Thessing Certified Teacher / Life Coach / Interior Designer
Transformational Retreats

Target Market(s)

Women Men General

Industry/Entity Type

Life Coaching

Contact Information for Business Card

www.velmoragrove.com
614-372-0583
Lina Suzette Brolin
Life Coach
Thessing Certified Teacher / Yoga Teacher / Interior Designer

Font styles to use
Serif
Decorative

Colors
33a6d6
e34197
ffc214

Requirements
Must have
• Quality Paper and touch /
Nice to have
• Beautiful Touch and feel
Should not have
• needs to be elegant

```html
<!DOCTYPE html>
<html lang="en">
<head>
<meta charset="utf-8">
<title>Velmora Grove Coaching – Business Card</title>
<link rel="stylesheet" href="https://fonts.googleapis.com/css2?family=Roboto:wght@500&family=Roboto+Condensed:wght@400&family=Open+Sans:wght@400&family=Cinzel:wght@500&display=swap">
<style>
  :root {
    --pink: #ff0a8c;
    --black: #000000;
    --white: #ffffff;
    --ink: #1a1a1a;
    --grey-text: #555555;
    --backdrop: #e4e4e4;
  }
  * { margin: 0; padding: 0; box-sizing: border-box; }
  html, body { width: 1200px; height: 1200px; overflow: hidden; }
  body { background: var(--backdrop); position: relative; }

  .card {
    position: absolute;
    left: 180px;
    width: 840px;
    height: 480px;
    border-radius: 30px;
    overflow: hidden;
  }
  .card--front { top: 90px; background: var(--white); }
  .card--back  { top: 630px; background: var(--pink); }

  .portrait {
    position: absolute;
    left: 185px; top: 92px;
    width: 188px; height: 218px;
    border: 1px solid #444;
    border-radius: 14px;
    background: linear-gradient(180deg, #f4f4f4 0%, #e8c98e 30%, #e0ac8a 60%, #c85a5a 88%, #333 100%);
  }

  .details { position: absolute; left: 439px; top: 108px; }
  .details__name {
    font-family: "Roboto", sans-serif;
    font-weight: 500;
    font-size: 28px;
    color: var(--pink);
    line-height: 1.1;
  }
  .details__roles {
    font-family: "Roboto Condensed", sans-serif;
    font-size: 19px;
    color: var(--ink);
    line-height: 24px;
    margin-top: 6px;
  }
  .details__contact {
    list-style: none;
    margin-top: 12px;
    font-family: "Open Sans", sans-serif;
    font-size: 19px;
    color: var(--grey-text);
  }
  .details__contact li { display: flex; align-items: center; gap: 10px; line-height: 27px; }
  .details__contact svg { width: 16px; height: 16px; flex: none; }

  .footer-band {
    position: absolute;
    left: 0; top: 389px;
    width: 100%; height: 52px;
    background: linear-gradient(90deg, var(--black) 0 700px, var(--pink) 700px 100%);
  }
  .footer-band__url {
    position: absolute;
    left: 0; width: 730px;
    top: 0; line-height: 52px;
    text-align: center;
    font-family: "Open Sans", sans-serif;
    font-size: 18px;
    letter-spacing: 2.4px;
    color: var(--white);
  }
  .badge {
    position: absolute;
    left: 668px; top: 384px;
    width: 62px; height: 62px;
    border-radius: 50%;
    background: var(--white);
    border: 3px solid var(--pink);
    display: flex; align-items: center; justify-content: center;
    font-family: "Cinzel", serif;
    font-weight: 500;
    font-size: 16px;
    color: var(--ink);
  }

  .brand {
    position: absolute;
    left: 0; top: 120px;
    width: 100%;
    text-align: center;
    color: var(--white);
    font-family: "Cinzel", serif;
    font-weight: 500;
  }
  .brand__mark {
    width: 130px; height: 130px;
    margin: 0 auto;
    border: 5px solid var(--white);
    border-radius: 50%;
    display: flex; align-items: center; justify-content: center;
    font-size: 38px;
  }
  .brand__name {
    margin-top: 28px;
    font-size: 27px;
    letter-spacing: 3px;
    line-height: 1;
  }
  .brand__sub {
    margin-top: 4px;
    font-size: 13px;
    letter-spacing: 19px;
    padding-left: 19px;
    line-height: 1;
  }
</style>
</head>
<body>
  <section class="card card--front" aria-label="Business card front">
    <div class="portrait" role="img" aria-label="Portrait photo of Lina Suzette Brolin"></div>
    <div class="details">
      <h1 class="details__name">Lina Suzette Brolin</h1>
      <p class="details__roles">Life Coach<br>Thessing Certified Teacher /<br>Yoga Teacher / Interior Designer</p>
      <ul class="details__contact">
        <li>
          <svg viewBox="0 0 16 16" aria-hidden="true"><path fill="#ff0a8c" d="M3.2 1.2l2.3-.4 1.3 3.3-1.5 1.2c.8 1.7 2 2.9 3.7 3.7l1.2-1.5 3.3 1.3-.4 2.3c-.2.8-.9 1.3-1.7 1.2C6 11.8 2.4 8.2 1.9 2.9c-.1-.8.5-1.5 1.3-1.7z"/></svg>
          614-372-0583
        </li>
        <li>
          <svg viewBox="0 0 16 16" aria-hidden="true"><rect x="1" y="3.5" width="14" height="9.5" fill="#ff0a8c"/><path d="M1.5 4l6.5 5 6.5-5" fill="none" stroke="#fff" stroke-width="1.3"/></svg>
          linasb@quorvamail.com
        </li>
      </ul>
    </div>
    <div class="footer-band"><span class="footer-band__url">www.velmoragrove.com</span></div>
    <div class="badge">Lina</div>
  </section>

  <section class="card card--back" aria-label="Business card back">
    <div class="brand">
      <div class="brand__mark">Lina</div>
      <p class="brand__name">VELMORA GROVE</p>
      <p class="brand__sub">COACHING</p>
    </div>
  </section>
</body>
</html>
```